Insurance Agency website design for Brellow Cover Insurance, LP

Build a website for Brellow Cover Insurance, LP which sells Homeowners, Auto, Renters, Condo, Flood, Disability, Life, Umbrella, and health insurance. We need the coolest insurance agency website out there to get quotes, contact us, or get additional information. Please list the following insurance companies we work with: Varnix, Ostle, Meridale Mutual, Quillor, Dunmarrow, KGZ, and Pellwick.

Make a design similar to https://www.fernagentry.com/

Selling personal insurance policies

```html
<!DOCTYPE html>
<html lang="en">
<head>
<meta charset="utf-8">
<title>Brellow Cover Insurance, LP</title>
<link href="https://fonts.googleapis.com/css2?family=Poppins:wght@400;500;600;700;800&display=swap" rel="stylesheet">
<style>
:root{
  --navy:#0c2a5c;
  --navy-deep:#071d43;
  --green:#1d7a2c;
  --green-dark:#16621f;
  --ink:#1b1b1b;
  --muted:#555b66;
  --band:#edf3fa;
  --line:#d9dee6;
  --white:#ffffff;
  --footer:#0a0a0a;
}
*{box-sizing:border-box;margin:0;padding:0}
html,body{width:1200px;height:4596px;overflow:hidden}
body{font-family:"Poppins",sans-serif;color:var(--ink);background:var(--white);position:relative}
a{color:inherit;text-decoration:none}
.btn{display:inline-flex;align-items:center;gap:8px;border-radius:30px;font-weight:600;font-size:14px;padding:12px 26px;color:var(--white)}
.btn-green{background:var(--green)}
.btn-navy{background:var(--navy)}
.arrow{width:14px;height:14px}

/* top bar */
.topbar{height:32px;background:var(--navy-deep);color:var(--white);font-size:13px;font-weight:600;display:flex;align-items:center;justify-content:space-between;padding:0 40px}
.topbar .account{display:flex;gap:22px;font-size:12px}

/* header */
.header{height:96px;display:flex;align-items:center;justify-content:space-between;padding:0 112px;background:var(--white)}
.brand{display:flex;align-items:center;gap:12px}
.brand-dot{width:34px;height:34px;border-radius:50%;background:var(--navy)}
.brand-name{font-weight:700;font-size:22px;color:var(--navy);line-height:1.1}
.nav{display:flex;align-items:center;gap:34px;font-size:14px;font-weight:600}
.nav .active{color:var(--green)}
.phone{display:flex;align-items:center;gap:10px}
.phone-icon{width:38px;height:38px;border-radius:50%;background:var(--green);display:flex;align-items:center;justify-content:center}
.phone small{display:block;font-size:11px;color:var(--muted);font-weight:500}
.phone strong{font-size:16px}

/* hero */
.hero{position:relative;height:552px}
.hero-photo{position:absolute;inset:0;background:linear-gradient(100deg,#2c4a6e 0%,#5b7896 40%,#9eb4c9 75%,#c9d6e2 100%)}
.hero-copy{position:absolute;left:112px;top:150px;color:var(--white)}
.hero-copy h1{font-size:40px;font-weight:800;letter-spacing:.5px}
.hero-copy p{font-size:34px;font-weight:500;line-height:1.25;margin:6px 0 28px}

/* agent finder */
.finder{position:absolute;left:112px;top:560px;width:976px;height:260px;background:var(--navy);color:var(--white);text-align:center;padding:32px 80px}
.finder h2{font-size:27px;font-weight:700;line-height:1.35}
.finder-form{display:flex;gap:26px;align-items:flex-end;justify-content:center;margin-top:24px;text-align:left}
.field label{display:block;font-size:13px;margin-bottom:8px}
.field .input{background:var(--white);color:#888;border-radius:24px;height:44px;display:flex;align-items:center;padding:0 20px;font-size:13px}
.field.address .input{width:360px}
.field.zip .input{width:300px}

/* about */
.about{position:absolute;top:920px;left:112px;width:976px;height:420px;display:flex;gap:80px;align-items:center}
.about-photo{width:400px;height:400px;border-radius:50%;background:radial-gradient(circle at 45% 40%,#c8a88a 0%,#8c6b52 45%,#5a4a44 100%);flex-shrink:0}
.about-copy h2{font-size:34px;font-weight:800;margin-bottom:20px}
.about-copy p{font-size:15px;line-height:1.75;color:var(--muted);margin-bottom:16px}

/* trusted */
.trusted{position:absolute;top:1440px;left:0;width:1200px;height:400px;background:var(--band);text-align:center}
.trusted h2{font-size:36px;font-weight:800;margin-top:110px}
.carrier-row{display:flex;align-items:center;justify-content:center;gap:60px;margin-top:70px;position:relative}
.carrier{font-size:24px;font-weight:700;color:var(--navy)}
.slide-btn{position:absolute;top:50%;transform:translateY(-50%);width:44px;height:44px;border-radius:50%;background:var(--white);box-shadow:0 2px 8px rgba(0,0,0,.12);display:flex;align-items:center;justify-content:center}
.slide-btn.prev{left:24px}.slide-btn.next{right:24px}

/* coverage */
.coverage{position:absolute;top:1960px;left:112px;width:976px;height:800px}
.coverage h2{font-size:38px;font-weight:800;text-align:center;line-height:1.3}
.coverage .hint{font-size:12px;font-weight:700;margin:42px 0 18px}
.coverage-grid{display:grid;grid-template-columns:repeat(4,220px);gap:32px 32px;justify-content:space-between}
.cover-card{height:220px;background:var(--white);box-shadow:0 3px 14px rgba(0,0,0,.1);position:relative;display:flex;flex-direction:column;align-items:center;justify-content:center;gap:24px}
.cover-card .check{position:absolute;left:14px;top:14px;width:22px;height:22px;border:1.5px solid #999;border-radius:3px}
.cover-icon{width:110px;height:90px;border-radius:10px;background:linear-gradient(135deg,#dfeee0,#c9e0cc)}
.cover-card span{font-size:17px;font-weight:700}
.coverage .more{display:flex;justify-content:center;margin-top:28px}

/* testimonials */
.testimonials{position:absolute;top:2820px;left:0;width:1200px;height:560px;background:linear-gradient(180deg,#1f7d2e,#166022);color:var(--white)}
.testimonials h2{font-size:38px;font-weight:800;text-align:center;margin-top:90px}
.quote-row{display:flex;justify-content:center;gap:40px;margin-top:50px;position:relative}
.quote-card{width:290px;background:var(--white);color:var(--ink);border-radius:8px;padding:26px 24px}
.quote-card.center{transform:translateY(-14px)}
.person{display:flex;align-items:center;gap:14px;margin-bottom:16px}
.avatar{width:58px;height:58px;border-radius:50%;background:linear-gradient(135deg,#8a6d5c,#3d3432)}
.person strong{display:block;font-size:15px}
.person small{color:#c0392b;font-size:12px}
.quote-card p{font-size:13px;line-height:1.6;color:var(--muted)}
.testimonials .slide-btn{top:50%}

/* quote */
.quote{position:absolute;top:3480px;left:112px;width:976px;height:600px;display:flex;gap:80px}
.quote-copy{width:400px;padding-top:30px}
.quote-copy h2{font-size:38px;font-weight:800;margin-bottom:20px}
.quote-copy p{font-size:14px;line-height:1.85;color:var(--muted)}
.quote-form{width:496px;height:580px;background:var(--navy);padding:40px 36px;display:flex;flex-direction:column;gap:18px}
.q-input{background:var(--white);height:46px;font-size:13px;color:#777;display:flex;align-items:center;justify-content:space-between;padding:0 18px}
.q-input.area{height:150px;align-items:flex-start;padding-top:14px}
.submit{align-self:center;color:var(--white);font-size:15px;text-decoration:underline;margin-top:8px}

/* footer */
.footer{position:absolute;top:4160px;left:0;width:1200px;height:436px;background:var(--footer);color:var(--white)}
.footer-cols{display:grid;grid-template-columns:repeat(4,1fr);gap:30px;padding:54px 112px 0}
.footer h3{font-size:22px;font-weight:700;margin-bottom:22px}
.footer li{list-style:none;font-size:14px;color:#cfd2d6;line-height:2}
.copyright{position:absolute;bottom:40px;width:100%;text-align:center;font-size:13px;color:#cfd2d6}
</style>
</head>
<body>

<div class="topbar">
  <span>Are you an independent agent?</span>
  <div class="account"><a href="#">&#128100; LOGIN</a><a href="#">&#128100; SIGN UP</a></div>
</div>

<header class="header">
  <div class="brand"><span class="brand-dot"></span><span class="brand-name">Brellow Cover<br>Insurance, LP</span></div>
  <nav class="nav">
    <a class="active" href="#">HOME</a>
    <a href="#">ABOUT US</a>
    <a class="btn btn-navy" href="#">GET A QUOTE
      <svg class="arrow" viewBox="0 0 16 16"><circle cx="8" cy="8" r="8" fill="#fff"/><path d="M6 4l4 4-4 4" stroke="#0c2a5c" stroke-width="2" fill="none"/></svg></a>
    <div class="phone">
      <span class="phone-icon"><svg width="18" height="18" viewBox="0 0 24 24"><path fill="#fff" d="M6.6 10.8a15 15 0 0 0 6.6 6.6l2.2-2.2c.3-.3.7-.4 1-.2 1.1.4 2.3.6 3.6.6.6 0 1 .4 1 1V20c0 .6-.4 1-1 1A17 17 0 0 1 3 4c0-.6.4-1 1-1h3.5c.6 0 1 .4 1 1 0 1.3.2 2.5.6 3.6.1.3 0 .7-.2 1z"/></svg></span>
      <div><small>Contact Us</small><strong>(555) 014-2290</strong></div>
    </div>
  </nav>
</header>

<section class="hero">
  <div class="hero-photo" role="img" aria-label="Photo of a blue umbrella held against city buildings"></div>
  <div class="hero-copy">
    <h1>PROTECT WHAT MATTERS MOST</h1>
    <p>Comprehensive Insurance Solutions<br>Tailored for You</p>
    <a class="btn btn-green" href="#">CONTACT US
      <svg class="arrow" viewBox="0 0 16 16"><circle cx="8" cy="8" r="8" fill="#fff"/><path d="M6 4l4 4-4 4" stroke="#1d7a2c" stroke-width="2" fill="none"/></svg></a>
  </div>
</section>

<section class="finder">
  <h2>The Address of your Personal Property Will Help in Finding The Right Local Agent for You.</h2>
  <div class="finder-form">
    <div class="field address"><label>Enter the address of your insurable property</label><div class="input">Start Typing your Address</div></div>
    <div class="field zip"><label>Enter the Zip Code</label><div class="input">Zip Code</div></div>
    <a class="btn btn-green" href="#">NEXT
      <svg class="arrow" viewBox="0 0 16 16"><circle cx="8" cy="8" r="8" fill="#fff"/><path d="M6 4l4 4-4 4" stroke="#1d7a2c" stroke-width="2" fill="none"/></svg></a>
  </div>
</section>

<section class="about">
  <div class="about-photo" role="img" aria-label="Photo of a couple meeting with an insurance agent"></div>
  <div class="about-copy">
    <h2>ABOUT US</h2>
    <p>Brellow Cover Insurance, LP is a full service, independent insurance agency with over three decades of experience in delivering comprehensive insurance solutions to individuals.</p>
    <p>We proudly offer a diverse portfolio of products from more than 25 of the most reputable and financially secure companies in the industry. Our dedicated team of over 50 skilled professionals is committed to customizing these products and services to meet the unique needs of each client.</p>
    <a class="btn btn-green" href="#">VIEW MORE
      <svg class="arrow" viewBox="0 0 16 16"><circle cx="8" cy="8" r="8" fill="#fff"/><path d="M6 4l4 4-4 4" stroke="#1d7a2c" stroke-width="2" fill="none"/></svg></a>
  </div>
</section>

<section class="trusted">
  <h2>OUR TRUSTED BY</h2>
  <div class="carrier-row">
    <span class="slide-btn prev"><svg width="14" height="14" viewBox="0 0 16 16"><path d="M10 3L5 8l5 5" stroke="#333" stroke-width="2" fill="none"/></svg></span>
    <span class="carrier">Varnix</span>
    <span class="carrier">Ostle</span>
    <span class="carrier">Meridale Mutual</span>
    <span class="carrier">Quillor</span>
    <span class="carrier">Dunmarrow</span>
    <span class="slide-btn next"><svg width="14" height="14" viewBox="0 0 16 16"><path d="M6 3l5 5-5 5" stroke="#333" stroke-width="2" fill="none"/></svg></span>
  </div>
</section>

<section class="coverage">
  <h2>WHAT TYPE OF PERSONAL PROTECTION<br>ARE YOU LOOKING FOR</h2>
  <p class="hint">SELECT UPTO 3 COVERAGES</p>
  <div class="coverage-grid">
    <div class="cover-card"><i class="check"></i><div class="cover-icon" role="img" aria-label="Car icon"></div><span>AUTO</span></div>
    <div class="cover-card"><i class="check"></i><div class="cover-icon" role="img" aria-label="House icon"></div><span>HOME</span></div>
    <div class="cover-card"><i class="check"></i><div class="cover-icon" role="img" aria-label="Hand holding house icon"></div><span>RENTERS</span></div>
    <div class="cover-card"><i class="check"></i><div class="cover-icon" role="img" aria-label="Condo building icon"></div><span>CONDO</span></div>
    <div class="cover-card"><i class="check"></i><div class="cover-icon" role="img" aria-label="Umbrella icon"></div><span>UMBRELLA</span></div>
    <div class="cover-card"><i class="check"></i><div class="cover-icon" role="img" aria-label="Mobile home icon"></div><span>MOBILE HOME</span></div>
    <div class="cover-card"><i class="check"></i><div class="cover-icon" role="img" aria-label="Motor home icon"></div><span>RV/MOTOR HOME</span></div>
    <div class="cover-card"><i class="check"></i><div class="cover-icon" role="img" aria-label="ATV icon"></div><span>ATV</span></div>
  </div>
  <div class="more"><a class="btn btn-green" href="#">VIEW MORE
    <svg class="arrow" viewBox="0 0 16 16"><circle cx="8" cy="8" r="8" fill="#fff"/><path d="M6 4l4 4-4 4" stroke="#1d7a2c" stroke-width="2" fill="none"/></svg></a></div>
</section>

<section class="testimonials">
  <h2>OUR TESTIMONIALS</h2>
  <div class="quote-row">
    <span class="slide-btn prev"><svg width="14" height="14" viewBox="0 0 16 16"><path d="M10 3L5 8l5 5" stroke="#333" stroke-width="2" fill="none"/></svg></span>
    <article class="quote-card">
      <div class="person"><div class="avatar" role="img" aria-label="Customer portrait"></div><div><strong>DANA WHITLOW</strong><small>Saint Charles, MO</small></div></div>
      <p>Switching our home and auto policies was simple. The team explained every option clearly and found us better coverage at a lower price. Highly recommend them.</p>
    </article>
    <article class="quote-card center">
      <div class="person"><div class="avatar" role="img" aria-label="Customer portrait"></div><div><strong>DANA WHITLOW</strong><small>Saint Charles, MO</small></div></div>
      <p>Switching our home and auto policies was simple. The team explained every option clearly and found us better coverage at a lower price. Highly recommend them.</p>
    </article>
    <article class="quote-card">
      <div class="person"><div class="avatar" role="img" aria-label="Customer portrait"></div><div><strong>DANA WHITLOW</strong><small>Saint Charles, MO</small></div></div>
      <p>Switching our home and auto policies was simple. The team explained every option clearly and found us better coverage at a lower price. Highly recommend them.</p>
    </article>
    <span class="slide-btn next"><svg width="14" height="14" viewBox="0 0 16 16"><path d="M6 3l5 5-5 5" stroke="#333" stroke-width="2" fill="none"/></svg></span>
  </div>
</section>

<section class="quote">
  <div class="quote-copy">
    <h2>GET A QUOTE</h2>
    <p>We believe that securing your home is one of the most important decisions you can make. Obtaining a comprehensive insurance quote is essential to understanding your coverage options and ensuring that your property is adequately protected against unforeseen events. Our team of experienced professionals is here to guide you through the process, helping you find the right policy that meets your specific needs and budget. Don't leave your home's safety to chance—get a quote today and take the first step towards peace of mind.</p>
  </div>
  <form class="quote-form">
    <div class="q-input">Name <span>&#128100;</span></div>
    <div class="q-input">Choose Services <span>&#9662;</span></div>
    <div class="q-input">Email Address <span>&#9993;</span></div>
    <div class="q-input">Phone Number <span>&#9742;</span></div>
    <div class="q-input area">Comments <span>&#9998;</span></div>
    <a class="submit" href="#">Submit Here</a>
  </form>
</section>

<footer class="footer">
  <div class="footer-cols">
    <div><h3>GET INSURED</h3><ul><li>Request a Quote</li><li>Match with an Insurance Company</li><li>National Insurance Directories</li><li>Insurance Agent Directory</li><li>Insurance Company Directory</li></ul></div>
    <div><h3>SHOP INSURANCE</h3><ul><li>Car Insurance</li><li>Homeowners Insurance</li><li>Life Insurance</li><li>Business Insurance</li><li>Workers Compensation Insurance</li><li>Health Insurance</li></ul></div>
    <div><h3>LEARN INSURANCE</h3><ul><li>Local Insurance Guides</li><li>Insurance Blog</li><li>Disaster Planning</li><li>Top Categories</li></ul></div>
    <div><h3>ABOUT US</h3><ul><li>Request a Quote</li><li>Match with an Insurance Company</li><li>National Insurance Directories</li><li>Insurance Agent Directory</li><li>Insurance Company Directory</li></ul></div>
  </div>
  <p class="copyright">Copyright©2025 All Rights Reserved</p>
</footer>

</body>
</html>
```